Oral Surgeon Referral Pads

Hello. We need referral pads for Dr Elsabet Quorvane, DDS board certified oral surgeon's new office - Harrowgate Dunmere Oral & Maxillofacial Surgery. See logo uploaded. See some images we would like included
Updates

Designs look the same

Font styles to use
Serif
Script

Colors
00AB8E
00BBA5
67D7C9
C6EFE9
E9F9F6

Requirements
Must have
• Color Pantone 623c. Also foldable business cards

```html
<!DOCTYPE html>
<html lang="en">
<head>
<meta charset="utf-8">
<title>Harrowgate Dunmere Oral &amp; Maxillofacial Surgery — Stationery</title>
<link rel="stylesheet" href="https://fonts.googleapis.com/css2?family=Open+Sans:wght@400;600&family=Arimo&family=Tinos:wght@400;700&display=swap">
<style>
:root{
  --backdrop:#d3d3d3;
  --paper:#ffffff;
  --teal-deep:#00ab8e;
  --teal:#00bba5;
  --teal-light:#67d7c9;
  --teal-pale:#c6efe9;
  --teal-mist:#e9f9f6;
  --rule-gray:#5a5a5a;
  --ink:#555555;
}
*{margin:0;padding:0;box-sizing:border-box}
html,body{width:1200px;height:1055px;overflow:hidden;background:var(--backdrop)}
.canvas{position:relative;width:1200px;height:1055px}
.sheet{position:absolute;background:var(--paper);overflow:hidden}

/* letterhead */
.letterhead{left:53px;top:122px;width:573px;height:811px}
.contact-list{position:absolute;list-style:none;font-family:"Tinos",serif;color:var(--ink)}
.letterhead .contact-list{left:37px;top:44px;font-size:9px;line-height:12px}
.contact-list li{display:flex;align-items:center;gap:5px;white-space:nowrap}
.contact-list svg{flex:none}
.address-block{position:absolute;right:38px;top:50px;text-align:right;font-family:"Tinos",serif;font-style:normal;font-size:9px;line-height:11.5px;color:var(--ink)}
.brand-lockup{position:absolute;text-align:center;font-family:"Open Sans",sans-serif;font-weight:400;color:var(--teal-deep);white-space:nowrap}
.brand-mark{display:block;margin:0 auto;border-radius:50%;border:2px solid var(--teal-light)}
.brand-name{display:block}
.brand-sub{display:block}
.letterhead .brand-lockup{left:0;width:573px;top:22px}
.letterhead .brand-mark{width:30px;height:30px;margin-bottom:15px}
.letterhead .brand-name{font-size:18px;line-height:22px}
.letterhead .brand-sub{font-size:10px;line-height:14px}
.band{position:absolute;height:7px}
.band.primary{background:var(--teal-deep)}
.band.secondary{background:var(--teal-light)}
.rule{position:absolute;height:2px;background:var(--rule-gray)}
.letterhead .band.primary{left:0;width:212px;top:95px}
.letterhead .band.secondary{left:360px;right:0;top:98px}
.letterhead .rule{left:0;right:0;top:108px}
.letter-body{position:absolute;left:51px;top:249px;width:474px;color:var(--ink)}
.salutation{font-family:"Open Sans",sans-serif;font-size:12.5px;margin-bottom:22px}
.letter-body p.copy{font-family:"Arimo",sans-serif;font-size:9.6px;line-height:11.9px;margin-bottom:10px}
.closing{font-family:"Open Sans",sans-serif;font-size:6.5px;margin-top:22px}
.signature-area{width:90px;height:26px;margin-top:18px;background:var(--teal-mist);border-radius:3px}

/* business card front */
.card-front{left:662px;top:333px;width:485px;height:278px;
  background:linear-gradient(90deg,var(--teal-light) 0%,var(--teal-light) 6%,var(--teal) 30%,var(--teal-deep) 50%,var(--teal-deep) 100%)}
.card-front .brand-lockup{left:0;width:485px;top:98px;color:#ffffff}
.card-front .brand-name{font-size:27px;line-height:34px}
.card-front .brand-sub{font-size:17px;line-height:22px;margin-top:6px}

/* business card back */
.card-back{left:662px;top:656px;width:485px;height:277px}
.card-back .brand-lockup{left:0;width:485px;top:30px}
.card-back .brand-mark{width:40px;height:40px;margin-bottom:14px}
.card-back .brand-name{font-size:20px;line-height:26px}
.card-back .brand-sub{font-size:11.5px;line-height:15px;margin-top:2px}
.card-back .band.primary{left:0;width:148px;top:115px;height:8px}
.card-back .band.secondary{left:335px;right:0;top:118px;height:8px}
.card-back .rule{left:0;right:0;top:135px}
.person{position:absolute;right:251px;top:172px;text-align:right;font-family:"Tinos",serif}
.person-name{font-size:17px;font-weight:700;color:var(--teal-deep);line-height:20px;letter-spacing:.3px}
.person-role{font-size:13px;color:var(--ink);line-height:16px}
.divider{position:absolute;left:242px;top:169px;width:1px;height:48px;background:var(--rule-gray)}
.card-back .contact-list{left:253px;top:166px;font-size:12.5px;line-height:17.5px}
.card-address{position:absolute;left:0;width:485px;top:243px;text-align:center;font-family:"Tinos",serif;font-size:13px;color:var(--ink)}
</style>
</head>
<body>
<main class="canvas">

  <section class="sheet letterhead" aria-label="Letterhead">
    <ul class="contact-list">
      <li><svg width="7" height="7" viewBox="0 0 10 10"><path d="M2 1l2 2-1 1.5c.8 1.5 1.6 2.3 3 3L7.5 6l2 2-1.5 1.5C4 9 1 6 .5 2z" fill="#00ab8e"/></svg>555-318-2740</li>
      <li><svg width="7" height="7" viewBox="0 0 10 10"><rect x="0.5" y="2" width="9" height="6" fill="#00ab8e"/><path d="M.5 2L5 5.5 9.5 2" stroke="#fff" fill="none"/></svg>office@harrowgatedunmere.com</li>
      <li><svg width="7" height="7" viewBox="0 0 10 10"><circle cx="5" cy="5" r="4.5" fill="#00ab8e"/><path d="M.5 5h9M5 .5c-2 2.5-2 6.5 0 9M5 .5c2 2.5 2 6.5 0 9" stroke="#fff" stroke-width=".8" fill="none"/></svg>www.harrowgatedunmere.com</li>
    </ul>

    <div class="brand-lockup">
      <span class="brand-mark"></span>
      <span class="brand-name">Harrowgate Dunmere</span>
      <span class="brand-sub">Oral &amp; Maxillofacial Surgery</span>
    </div>

    <address class="address-block">Your address<br>city<br>state, ZIP 0000</address>

    <div class="band primary"></div>
    <div class="band secondary"></div>
    <div class="rule"></div>

    <article class="letter-body">
      <p class="salutation">Dear Mr. Pellow,</p>
      <p class="copy">Lorem ipsum dolor sit amet, consectetuer adipiscing elit, sed diam nonmmy nibh euismod tincidunt ut laor eet dolore magna aliquam erat volutpat. Ut wisi enim ad minim veniam, quis nostrud exerci tationmcorper suscipit lobortis nisl ut aliquip ex ea commodo consequat. Duis autem vel eum iriure dolor in hendrerit in vulputate velit esse molestie consequat, vel illum dolore eu feugiat</p>
      <p class="copy">Rorem ipsum dolor sit amet, consectetuer adipiscing elit, sed diam nonmmy nibh euismod tincidunt ut laor eet dolore magna aliquam erat volutpat. Ut wisi enim ad minim veniam, quis nostrud exerci tationmcorper suscipit lobortis nisl ut aliquip ex ea commodo consequat. Duis autem vel eum iriure dolor in hendrerit in vulputate velit esse molest</p>
      <p class="copy">Dorem ipsum dolor sit amet, consectetuer adipiscing elit, sed diam nonmmy nibh euismod tincidunt ut laor eet dolore magna aliquam erat volutpat. Ut wisi enim ad minim veniam, quis nostrud exerci tationmcorper suscipit lobortis nisl ut aliquip ex ea commodo consequat. Duis autem vel eum iriure dolor in hendrerit in suscipit lobortis nisl ut aliquip ex ea commodo consequat. Duis autem vel eum iriure dolor in hendrerit in vulputate velit esse molestie consequat, vel illum</p>
      <p class="copy">Sorem ipsum dolor sit amet, consectetuer adipiscing elit, sed diam nonmmy nibh euismod tincidunt ut laor eet dolore magna aliquam erat volutpat. Ut wisi enim ad minim veniam, quis nostrud exerci tationmcorper suscipit lobortis nisl ut aliquip ex ea commodo consequat. Duis autem vel eum iriure dolor in</p>
      <p class="closing">Sincerely,</p>
      <div class="signature-area" role="img" aria-label="Handwritten signature of Dr Elsabet Quorvane"></div>
    </article>
  </section>

  <section class="sheet card-front" aria-label="Business card front">
    <div class="brand-lockup">
      <span class="brand-name">Harrowgate Dunmere</span>
      <span class="brand-sub">Oral &amp; Maxillofacial Surgery</span>
    </div>
  </section>

  <section class="sheet card-back" aria-label="Business card back">
    <div class="brand-lockup">
      <span class="brand-mark"></span>
      <span class="brand-name">Harrowgate Dunmere</span>
      <span class="brand-sub">Oral &amp; Maxillofacial Surgery</span>
    </div>
    <div class="band primary"></div>
    <div class="band secondary"></div>
    <div class="rule"></div>

    <div class="person">
      <p class="person-name">TOBIAS RENWICK</p>
      <p class="person-role">Manager</p>
    </div>
    <div class="divider"></div>
    <ul class="contact-list">
      <li><svg width="10" height="10" viewBox="0 0 10 10"><path d="M2 1l2 2-1 1.5c.8 1.5 1.6 2.3 3 3L7.5 6l2 2-1.5 1.5C4 9 1 6 .5 2z" fill="none" stroke="#00ab8e"/></svg>555-318-2740</li>
      <li><svg width="10" height="10" viewBox="0 0 10 10"><rect x="0.5" y="2" width="9" height="6" fill="none" stroke="#00ab8e"/><path d="M.5 2L5 5.5 9.5 2" stroke="#00ab8e" fill="none"/></svg>office@harrowgatedunmere.com</li>
      <li><svg width="10" height="10" viewBox="0 0 10 10"><circle cx="5" cy="5" r="4.5" fill="none" stroke="#00ab8e"/><path d="M.5 5h9M5 .5c-2 2.5-2 6.5 0 9M5 .5c2 2.5 2 6.5 0 9" stroke="#00ab8e" stroke-width=".8" fill="none"/></svg>www.harrowgatedunmere.com</li>
    </ul>
    <p class="card-address">Your Address, City, State, Zip 0000</p>
  </section>

</main>
</body>
</html>
```